Business Card Design For A Renovation Contractor Company

We need a business card for a new company based in Singapore, our company name is "RB Tolvane". We are a renovation contractor that builds designs into reality. We build more of F&B restaurants, retail stores and commercial offices. We work very closely with designers. The final design should communicate to our client that we are a company that you can trust, that will plan and complete your project without giving you a headache. I like my client to remember my company as "RB". The beauty of SIMPLE is important.

Industry/Entity Type

Contractor

Requirements
Nice to have
• Black or Red base

```html
<!DOCTYPE html>
<html lang="en">
<head>
<meta charset="utf-8">
<title>RB Tolvane – Business Card</title>
<link href="https://fonts.googleapis.com/css2?family=Questrial&family=Montserrat:wght@700&display=swap" rel="stylesheet">
<style>
  :root {
    --brand-red: #e8202a;
    --ink: #231f20;
    --grey: #555555;
    --paper: #ffffff;
    --stage: #ecebe8;
  }
  * { margin: 0; padding: 0; box-sizing: border-box; }
  html, body { width: 1200px; height: 720px; overflow: hidden; }
  body {
    background: var(--stage);
    font-family: "Questrial", "Century Gothic", sans-serif;
    position: relative;
  }
  .card {
    position: absolute;
    width: 540px;
    height: 309px;
    overflow: hidden;
    box-shadow: 0 6px 18px rgba(0,0,0,0.18);
  }
  .card--front { left: 40px; top: 120px; background: var(--paper); }
  .card--back  { left: 620px; top: 290px; background: var(--brand-red); }

  .front-wave { position: absolute; inset: 0; width: 540px; height: 309px; }

  .brand {
    position: absolute; left: 34px; top: 62px;
    display: flex; align-items: center; gap: 12px;
  }
  .brand__dot {
    width: 44px; height: 44px; border-radius: 50%;
    border: 5px solid var(--brand-red);
  }
  .brand__name { font-size: 32px; color: var(--ink); letter-spacing: -0.5px; line-height: 1; }
  .tagline {
    position: absolute; left: 34px; top: 116px; width: 236px;
    font-size: 13px; color: var(--ink);
    border-top: 2px solid var(--ink); padding-top: 1px;
    text-align: center; white-space: nowrap;
  }

  .divider {
    position: absolute; left: 292px; top: 30px; width: 1px; height: 118px;
    background: #cfcfcf;
  }
  .contact { position: absolute; left: 306px; top: 28px; }
  .contact__name { font-family: "Montserrat", sans-serif; font-weight: 700; font-size: 17px; color: var(--brand-red); }
  .contact__title { font-size: 14px; color: var(--grey); margin-bottom: 4px; }
  .contact__list { list-style: none; }
  .contact__item { display: flex; align-items: center; gap: 8px; font-size: 13.5px; color: var(--ink); line-height: 19px; }
  .contact__icon { width: 11px; height: 11px; flex: none; }

  .address {
    position: absolute; left: 170px; top: 262px;
    font-size: 13.5px; color: var(--paper); white-space: nowrap;
    transform: rotate(-9deg); transform-origin: left center;
  }

  .back-brand {
    position: absolute; left: 0; right: 0; top: 92px;
    display: flex; justify-content: center; align-items: center; gap: 16px;
  }
  .back-brand__dot { width: 58px; height: 58px; border-radius: 50%; border: 7px solid var(--paper); }
  .back-brand__name { font-size: 48px; color: var(--paper); line-height: 1; }
  .back-url {
    position: absolute; left: 0; right: 0; bottom: 34px; text-align: center;
    font-size: 17px; letter-spacing: 3px; color: var(--paper);
  }
</style>
</head>
<body>
  <section class="card card--front" aria-label="Business card front">
    <svg class="front-wave" viewBox="0 0 540 309" aria-hidden="true">
      <path d="M0,180 C160,206 340,196 540,156 L540,168 C340,210 160,220 0,192 Z" fill="var(--ink)"/>
      <path d="M0,192 C160,220 340,210 540,168 L540,309 L0,309 Z" fill="var(--brand-red)"/>
    </svg>

    <div class="brand">
      <span class="brand__dot"></span>
      <span class="brand__name">RB Tolvane</span>
    </div>
    <p class="tagline">turning plans into real spaces</p>

    <div class="divider"></div>
    <div class="contact">
      <p class="contact__name">Your Name</p>
      <p class="contact__title">Title</p>
      <ul class="contact__list">
        <li class="contact__item">
          <svg class="contact__icon" viewBox="0 0 12 12"><circle cx="6" cy="6" r="6" fill="var(--brand-red)"/><path d="M4 3.2 L5 3 L5.6 4.8 L4.9 5.3 Q5.6 6.8 6.8 7.3 L7.3 6.6 L9 7.2 L8.8 8.2 Q5 8.6 3.6 4.2 Z" fill="#fff"/></svg>
          123-456-7890
        </li>
        <li class="contact__item">
          <svg class="contact__icon" viewBox="0 0 12 12"><circle cx="6" cy="6" r="6" fill="var(--brand-red)"/><rect x="4.2" y="2.6" width="3.6" height="6.8" rx="0.6" fill="#fff"/></svg>
          456-207-1938
        </li>
        <li class="contact__item">
          <svg class="contact__icon" viewBox="0 0 12 12"><circle cx="6" cy="6" r="6" fill="var(--brand-red)"/><rect x="3" y="4" width="6" height="4.2" fill="#fff"/><path d="M3 4 L6 6.4 L9 4" stroke="var(--brand-red)" stroke-width="0.7" fill="none"/></svg>
          info@rbtolvane.com
        </li>
        <li class="contact__item">
          <svg class="contact__icon" viewBox="0 0 12 12"><circle cx="6" cy="6" r="6" fill="var(--brand-red)"/><circle cx="6" cy="6" r="3.2" stroke="#fff" stroke-width="0.8" fill="none"/><path d="M2.8 6 H9.2 M6 2.8 V9.2" stroke="#fff" stroke-width="0.7"/></svg>
          www.rbtolvane.com
        </li>
      </ul>
    </div>

    <p class="address">Door No. Street Name City Name, State, Zip Code.</p>
  </section>

  <section class="card card--back" aria-label="Business card back">
    <div class="back-brand">
      <span class="back-brand__dot"></span>
      <span class="back-brand__name">RB Tolvane</span>
    </div>
    <p class="back-url">www.rbtolvane.com</p>
  </section>
</body>
</html>
```